Desktop and Networking Support Course 9.17.25

Important the ad should not be very busy with the text taking up the major part of the ad .. please do not make the text so big that it takes up most of the ad..
Flyer Design Brief for Graphic Artist
also i am looking for something unique or creative that it will stand out .
Size & Layout:
Full Page with Bleed: 8” x 10.75” + 0.25” bleed on all sides.
Footer Space: Leave a 1-inch margin at the bottom for footer content (e.g., contact info, logo, or call-to-action).
Target Audience:
College-age students (around 24 years old)
Located in the USA
Interested in creative, professional, and career-building opportunities
Purpose:
To attract students to enroll in a college program
Flyer should be eye-catching, unique, and creative
Text must be clear and readable,
Design Style:
Use vector art, typography, or photography — your choice
If using photography, feature a white young professional USA citizen:
Wearing a white collared shirt
not with long hair
Creative Direction:
The flyer should stand out visually — something people would want to look at and keep
Showcase creativity and professionalism
Use bold colors, dynamic layout, or unexpected design elements to grab attention
Avoid clutter — keep the design balanced and clean
Text Suggestions (can be adjusted):
Footer,
please leave one inch on the bottom for the footer

```html
<!DOCTYPE html>
<html lang="en">
<head>
<meta charset="utf-8">
<title>Desktop &amp; Network Support Course</title>
<link rel="stylesheet" href="https://fonts.googleapis.com/css2?family=Montserrat:wght@400;500;700;800&display=swap">
<style>
  :root {
    --teal-bg: #5f9c9c;
    --teal-dark: #237d80;
    --teal-deep: #217579;
    --teal-mid: #72acad;
    --teal-soft: #6fb0af;
    --mist: #dfeceb;
    --white: #ffffff;
    --ink: #2b2b2b;
    --heading-teal: #2b8286;
  }
  * { margin: 0; padding: 0; box-sizing: border-box; }
  html, body { width: 893px; height: 1200px; overflow: hidden; background: var(--white); }
  body { font-family: "Montserrat", Arial, sans-serif; }
  .flyer { position: relative; width: 893px; height: 1200px; overflow: hidden; background: var(--white); }
  .backdrop { position: absolute; inset: 0; }
  .headline-top {
    position: absolute; left: 42px; top: 76px;
    font-weight: 800; font-size: 71px; letter-spacing: -1px; line-height: 1;
    color: var(--white); white-space: nowrap;
    text-shadow: 0 3px 8px rgba(0,0,0,0.18);
  }
  .headline-box {
    position: absolute; left: 44px; top: 166px; width: 501px; height: 74px;
    background: var(--white);
    display: flex; align-items: center; justify-content: center;
  }
  .headline-box span {
    font-weight: 800; font-size: 52px; letter-spacing: -0.5px; line-height: 1;
    color: var(--heading-teal); white-space: nowrap;
  }
  .highlights { position: absolute; left: 44px; top: 279px; list-style: none; }
  .highlights li {
    display: flex; align-items: center; height: 40px;
    font-weight: 500; font-size: 21.5px; color: var(--white); white-space: nowrap;
  }
  .highlights svg { width: 20px; height: 18px; margin-right: 17px; }
  .jobs { position: absolute; left: 0; width: 893px; top: 760px; text-align: center; }
  .jobs h2 { font-weight: 700; font-size: 28.5px; color: var(--heading-teal); letter-spacing: 0.2px; }
  .jobs p { font-weight: 400; font-size: 25px; color: var(--ink); margin-top: 8px; }
  .features { position: absolute; top: 862px; left: 0; width: 893px; height: 58px; }
  .feature { position: absolute; display: flex; align-items: center; height: 56px; }
  .feature svg { flex: none; }
  .feature span { font-weight: 500; font-size: 16.5px; line-height: 25px; color: var(--ink); margin-left: 11px; }
  .f1 { left: 85px; } .f2 { left: 380px; } .f3 { left: 659px; }
  .footer-band { position: absolute; left: 0; top: 1011px; width: 893px; height: 189px; background: var(--mist); }
  .banner {
    position: absolute; left: 141px; top: 965px; width: 611px; height: 92px;
    background: var(--teal-soft); padding: 8px;
  }
  .banner-inner {
    width: 100%; height: 100%; background: var(--teal-deep);
    display: flex; align-items: center; justify-content: center; gap: 20px;
    color: var(--white); font-weight: 500; font-size: 16.7px; white-space: nowrap;
  }
  .frame { position: absolute; inset: 0; pointer-events: none; }
</style>
</head>
<body>
<div class="flyer">
  <svg class="backdrop" width="893" height="1200" viewBox="0 0 893 1200">
    <defs>
      <linearGradient id="portraitTone" x1="0" y1="0" x2="0" y2="1">
        <stop offset="0" stop-color="#c9d3d3"/>
        <stop offset="0.45" stop-color="#eef1f1"/>
        <stop offset="1" stop-color="#8f9696"/>
      </linearGradient>
    </defs>
    <rect width="893" height="720" fill="var(--teal-bg)"/>
    <path d="M0,420 C60,450 120,458 200,462 C290,466 350,500 380,600 L380,720 L0,720 Z" fill="var(--teal-dark)"/>
    <path d="M0,548 C70,528 140,508 210,502 C290,496 340,530 378,590 L378,720 L0,720 Z" fill="var(--teal-mid)"/>
    <g role="img" aria-label="Photo of a young professional with short hair in a white collared shirt, smiling">
      <path d="M600,60 C680,40 760,70 800,150 C830,230 810,290 780,320 C850,350 893,380 893,420 L893,720 L520,720 L560,380 C600,340 650,330 660,300 C620,260 590,200 600,60 Z" fill="url(#portraitTone)"/>
    </g>
    <path d="M0,580 C60,592 130,578 200,556 C280,535 335,528 365,570 C405,625 430,692 525,708 C620,720 720,686 790,668 C840,656 870,662 893,670 L893,1200 L0,1200 Z" fill="var(--white)"/>
    <path d="M780,666 C820,654 860,652 893,660 L893,672 C865,664 830,664 790,670 Z" fill="var(--teal-dark)"/>
    <path d="M505,378 L520,376 C545,370 570,350 580,320 C592,285 585,270 565,262" fill="none" stroke="var(--white)" stroke-width="1.6" stroke-dasharray="6 5"/>
    <circle cx="525" cy="351" r="14" fill="none" stroke="var(--white)" stroke-width="1.6" stroke-dasharray="5 4"/>
    <path d="M558,249 L579,262 L570,264 L575,276 L569,278 L564,267 L558,273 Z" fill="var(--white)"/>
  </svg>

  <div class="headline-top">Your Career Is</div>
  <div class="headline-box"><span>Just a Click Away</span></div>

  <ul class="highlights">
    <li><svg viewBox="0 0 20 18"><path d="M2,2 L9,9 L2,16 M10,2 L17,9 L10,16" fill="none" stroke="#fff" stroke-width="2.6"/></svg>Desktop &amp; Network Support Course</li>
    <li><svg viewBox="0 0 20 18"><path d="M2,2 L9,9 L2,16 M10,2 L17,9 L10,16" fill="none" stroke="#fff" stroke-width="2.6"/></svg>Master Corvex Operating Systems</li>
    <li><svg viewBox="0 0 20 18"><path d="M2,2 L9,9 L2,16 M10,2 L17,9 L10,16" fill="none" stroke="#fff" stroke-width="2.6"/></svg>90% Employment Rate – Class of 2024</li>
  </ul>

  <section class="jobs">
    <h2>Prepare for 3 of the Top 10 Tech Jobs</h2>
    <p>National Career Outlook Report 2025</p>
  </section>

  <div class="features">
    <div class="feature f1">
      <svg width="65" height="50" viewBox="0 0 65 50">
        <rect x="16" y="0" width="49" height="36" rx="4" fill="var(--teal-soft)"/>
        <rect x="34" y="38" width="4" height="6" fill="var(--teal-dark)"/>
        <rect x="24" y="44" width="24" height="3" fill="var(--teal-dark)"/>
        <circle cx="9" cy="12" r="5" fill="var(--teal-dark)"/>
        <path d="M1,22 Q1,18 6,18 L12,18 L24,12 L26,15 L15,25 L15,48 L3,48 L3,34 L1,34 Z" fill="var(--teal-dark)"/>
      </svg>
      <span>Hands-On Desktop &amp;<br>Network Training</span>
    </div>
    <div class="feature f2">
      <svg width="57" height="56" viewBox="0 0 57 56">
        <rect x="1" y="9" width="50" height="36" rx="3" fill="none" stroke="var(--teal-dark)" stroke-width="3"/>
        <rect x="5" y="14" width="42" height="27" fill="var(--teal-soft)"/>
        <circle cx="26" cy="10" r="7" fill="var(--white)" stroke="var(--teal-dark)" stroke-width="3"/>
        <rect x="20" y="45" width="12" height="5" fill="var(--teal-dark)"/>
        <rect x="12" y="50" width="28" height="3" fill="var(--teal-dark)"/>
        <path d="M45,30 L57,52 L33,52 Z" fill="var(--teal-dark)"/>
        <rect x="44" y="37" width="2" height="8" fill="#fff"/><rect x="44" y="47" width="2" height="2" fill="#fff"/>
      </svg>
      <span>Real-World<br>Troubleshooting Skills</span>
    </div>
    <div class="feature f3">
      <svg width="57" height="56" viewBox="0 0 57 56">
        <path d="M18,16 A10,10 0 0 1 38,16 Z" fill="var(--teal-dark)"/>
        <circle cx="28" cy="14" r="4" fill="#fff"/>
        <rect x="5" y="18" width="46" height="30" fill="var(--teal-soft)"/>
        <rect x="0" y="49" width="57" height="5" fill="var(--teal-dark)"/>
      </svg>
      <span>Ready for<br>IT Jobs</span>
    </div>
  </div>

  <div class="footer-band"></div>
  <div class="banner">
    <div class="banner-inner">
      <span>In-Person and Remote Options</span><span>|</span><span>Partial Scholarships Offered</span>
    </div>
  </div>

  <svg class="frame" width="893" height="1200" viewBox="0 0 893 1200">
    <path d="M28,583 L28,28 L865,28 L865,680" fill="none" stroke="var(--white)" stroke-width="1.3"/>
    <path d="M28,583 L28,1172 L865,1172 L865,680" fill="none" stroke="var(--teal-dark)" stroke-width="1.3"/>
  </svg>
</div>
</body>
</html>
```